Tallow Reed Software

We are a software company selling endpoint visibility, access and security technology to enterprise-level IT departments.

Our technology helps organizations gain comprehensive visibility into and control over devices accessing their corporate network so they can quickly identify and address suspicious activity on the network that could lead to potential threats like data breaches.

This technology can cost organizations upwards of $1M - depending on the size of the organization. Our primary clients are Pinnacle 2,000 companies.

We want a professional, polished business card to represent our new brand.

Info fields to include on the card:
Name
Job Title
Office Phone #
Cell Phone #
Email address
Address: 4270 Vestridge Pond Blvd., Ste. 2600, Corvallen, IA 55812
Website address: www.tallowreedsoftware.example
Tagline: See every edge. Secure the whole.

Logo files and color specs document are attached. Would like color scheme to coordinate with the logo.

Also looking at stationary/envelope designs in conjunction with the business card designs. Received very few designs that included the stationary.

Software

```html
<!DOCTYPE html>
<html lang="en">
<head>
<meta charset="utf-8">
<title>Tallow Reed Software — Stationery</title>
<link href="https://fonts.googleapis.com/css2?family=Montserrat:wght@400;500;600&family=Allura&display=swap" rel="stylesheet">
<style>
  :root {
    --brand-red: #8f3f3f;
    --brand-red-deep: #7c3434;
    --paper: #f7f7f7;
    --envelope: #ffffff;
    --ink: #5a5a5a;
    --ink-soft: #8a8a8a;
    --backdrop: #d9d9d9;
  }
  * { box-sizing: border-box; margin: 0; padding: 0; }
  html, body { width: 1200px; height: 800px; overflow: hidden; }
  body {
    background: var(--backdrop);
    font-family: "Montserrat", sans-serif;
    position: relative;
  }
  .sheet { position: absolute; box-shadow: 0 6px 18px rgba(0,0,0,.18); overflow: hidden; }

  .brand-name {
    display: flex; align-items: center; gap: 7px;
    color: var(--brand-red); font-weight: 600; letter-spacing: .12em;
    text-transform: uppercase; font-size: 11px; line-height: 1.2;
  }
  .brand-name__square { width: 8px; height: 8px; background: var(--brand-red); flex: none; }

  /* Letterhead */
  .letterhead {
    left: 40px; top: 120px; width: 396px; height: 560px;
    background: var(--paper); padding: 34px 32px 28px;
    color: var(--ink);
  }
  .letterhead__top { display: flex; justify-content: space-between; align-items: flex-start; gap: 12px; }
  .contact { font-size: 5.6px; line-height: 1.55; }
  .contact dt { color: var(--brand-red); font-weight: 600; float: left; width: 20px; }
  .contact dd { margin-left: 20px; }
  .contact .contact__address { margin-top: 2px; }
  .letter-body { margin-top: 46px; font-size: 6.6px; line-height: 1.6; color: var(--ink-soft); }
  .letter-body .salutation { color: var(--ink); font-weight: 600; margin-bottom: 10px; }
  .letter-body p { margin-bottom: 9px; }
  .signature { margin-top: 22px; }
  .signature__script { font-family: "Allura", cursive; font-size: 22px; color: #333; line-height: 1; }
  .signature__role { font-size: 6px; font-weight: 600; color: #333; }
  .letterhead__accent {
    position: absolute; right: 0; bottom: 0; width: 110px; height: 130px;
    background: radial-gradient(circle at 100% 100%, rgba(0,0,0,.10), rgba(0,0,0,0) 70%);
  }

  /* Folder */
  .folder {
    left: 470px; top: 140px; width: 380px; height: 520px;
    background: var(--brand-red); color: #fff;
    padding: 70px 40px;
  }
  .folder .brand-name { color: #fff; font-size: 17px; letter-spacing: .14em; gap: 10px; }
  .folder .brand-name__square { background: #fff; width: 12px; height: 12px; }
  .tagline { margin-top: 8px; font-size: 9px; letter-spacing: .03em; opacity: .9; }
  .folder__accent {
    position: absolute; left: 0; bottom: 0; width: 240px; height: 260px;
    background: radial-gradient(circle at 20% 80%, rgba(255,255,255,.28), rgba(255,255,255,0) 70%);
  }

  /* Envelopes */
  .envelope { left: 880px; width: 290px; height: 150px; background: var(--envelope); }
  .envelope--front { top: 170px; padding: 26px 24px; }
  .envelope--front .brand-name { font-size: 8.5px; gap: 6px; }
  .envelope--front .brand-name__square { width: 6px; height: 6px; }
  .return-address { margin-top: 6px; margin-left: 12px; font-size: 5px; line-height: 1.55; color: var(--ink-soft); }
  .envelope__accent {
    position: absolute; right: 0; top: 0; width: 80px; height: 90px;
    background: radial-gradient(circle at 100% 40%, rgba(0,0,0,.08), rgba(0,0,0,0) 70%);
  }
  .envelope--back { top: 400px; }
  .envelope__flap { position: relative; height: 52px; background: var(--brand-red); }
  .envelope__flap-accent {
    position: absolute; left: 115px; top: 6px; width: 60px; height: 40px;
    background: radial-gradient(circle, rgba(255,255,255,.35), rgba(255,255,255,0) 70%);
  }
  .envelope__fold { position: absolute; left: 0; top: 52px; width: 100%; height: 98px; }
</style>
</head>
<body>

  <article class="sheet letterhead">
    <header class="letterhead__top">
      <div class="brand-name"><span class="brand-name__square"></span>Tallow Reed Software</div>
      <dl class="contact">
        <dt>phone</dt><dd>1-800-555-0147</dd>
        <dt>cell</dt><dd>1-800-555-0162</dd>
        <dt>email</dt><dd>sales@tallowreedsoftware.example</dd>
        <dd class="contact__address">4270 Vestridge Pond Blvd., Ste. 2600<br>Corvallen, IA 55812<br>www.tallowreedsoftware.example</dd>
      </dl>
    </header>
    <section class="letter-body">
      <p class="salutation">Lorem ipsum,</p>
      <p>Cras mattis consectetur purus sit amet fermentum. Etiam porta sem malesuada magna mollis euismod. Integer posuere erat a ante venenatis dapibus posuere velit aliquet.</p>
      <p>Vivamus sagittis lacus vel augue laoreet rutrum faucibus dolor auctor. Donec sed odio dui. Nullam quis risus eget urna mollis ornare vel eu leo.</p>
      <p>Donec id elit non mi porta gravida at eget metus. Fusce dapibus tellus ac cursus commodo, tortor mauris condimentum nibh, ut fermentum massa justo sit amet risus.</p>
      <p>Cum sociis natoque penatibus et magnis dis parturient montes, nascetur ridiculus mus. Maecenas faucibus mollis interdum.</p>
      <p>Cras justo odio, dapibus ac facilisis in, egestas eget quam. Sed posuere consectetur est at lobortis.</p>
    </section>
    <footer class="signature">
      <div class="signature__script">Your Name</div>
      <div class="signature__role">Company Director</div>
    </footer>
    <div class="letterhead__accent" role="img" aria-label="Faint grey dot pattern in the lower corner"></div>
  </article>

  <article class="sheet folder">
    <div class="brand-name"><span class="brand-name__square"></span>Tallow Reed Software</div>
    <p class="tagline">See every edge. Secure the whole.</p>
    <div class="folder__accent" role="img" aria-label="Large white and translucent dot pattern in the lower left"></div>
  </article>

  <article class="sheet envelope envelope--front">
    <div class="brand-name"><span class="brand-name__square"></span>Tallow Reed Software</div>
    <p class="return-address">4270 Vestridge Pond Blvd., Ste. 2600<br>Corvallen, IA 55812</p>
    <div class="envelope__accent" role="img" aria-label="Faint grey dot pattern at the right edge"></div>
  </article>

  <article class="sheet envelope envelope--back">
    <div class="envelope__flap">
      <div class="envelope__flap-accent" role="img" aria-label="Small white dot pattern centred on the flap"></div>
    </div>
    <svg class="envelope__fold" viewBox="0 0 290 98" preserveAspectRatio="none">
      <polyline points="0,98 145,30 290,98" fill="none" stroke="#e6e6e6" stroke-width="1"/>
    </svg>
  </article>

</body>
</html>
```